Looking for a dynamic business card for a pizzeria.

A business card with our food, logo, and space for name, title, email, website, phone. The card should convey quality, unique, amazing. On the front, I envision food photo or photos with the owners names and contact information. On the back, more food with locations, website, facebook, twitter, instagram icons. It should look polished, not cartoonish, or plain.
Target Market(s)
upscale, local food buyers, 30-50 years in age.
Industry/Entity Type
Restaurant
Contact Information for Business Card
Business Name: Bru'nettix, LLC
Website: www.brunettix.com
Back:
2 locations: (can list on the back of card)
1. Harborview
4087 Corlan Avenue
Marlow Bay, WA 97061
555-481-5067
2. Crestmont Hill
7315 Wendmere Road
Marlow Bay, WA 97064
555-293-8840
front:
EDITABLE space for
Business name
Person's Name
title
2nd title
Email address
cell-phone number
Requirements
Must have
- logo
- my food photo or photos (no watermarks showing)
- locations on back
- Person contact information on front
- full bleed

```html
<!DOCTYPE html>
<html lang="en">
<head>
<meta charset="utf-8">
<title>Bru'nettix Business Card</title>
<link rel="stylesheet" href="https://fonts.googleapis.com/css2?family=Jost:wght@400;500;600;700&display=swap">
<style>
  :root {
    --page: #e9e6e1;
    --red: #b3120f;
    --green: #1f5a2c;
    --cream: #fbf6ea;
    --white: #ffffff;
    --photo-dark: #3a3936;
    --photo-dough: #d8b48a;
    --photo-light: #9c9a95;
  }
  * { box-sizing: border-box; margin: 0; padding: 0; }
  html, body {
    width: 1200px; height: 843px; overflow: hidden;
    background: var(--page);
    font-family: "Jost", "Futura", sans-serif;
  }
  .stage { position: relative; width: 1200px; height: 843px; }
  .card {
    position: absolute; left: 290px; width: 620px; height: 354px;
    overflow: hidden;
    box-shadow: 0 6px 18px rgba(0,0,0,0.18);
  }
  .card--front { top: 52px; }
  .card--back { top: 438px; background: var(--cream); }

  /* Front: photo card */
  .card__photo {
    position: absolute; inset: 0;
    background:
      radial-gradient(ellipse 55% 60% at 45% 62%, var(--photo-dough) 0%, #b98d62 55%, transparent 80%),
      linear-gradient(160deg, var(--photo-light) 0%, #6b6964 45%, var(--photo-dark) 100%);
  }
  .card__photo-shade {
    position: absolute; inset: 0;
    background: linear-gradient(180deg, rgba(0,0,0,0) 50%, rgba(0,0,0,0.45) 100%);
  }
  .brand {
    position: absolute; display: flex; align-items: center; gap: 10px;
    font-weight: 600; letter-spacing: 1px; white-space: nowrap;
  }
  .brand--front { top: 62px; left: 220px; color: var(--red); font-size: 42px; }
  .brand__dot { width: 34px; height: 34px; border-radius: 50%; background: var(--red); }
  .social { position: absolute; top: 96px; right: 26px; display: flex; gap: 8px; }
  .social__dot { width: 16px; height: 16px; border-radius: 50%; background: var(--white); }
  .locations {
    position: absolute; left: 24px; bottom: 22px; color: var(--white);
    font-size: 15px; line-height: 1.35;
  }
  .location__name {
    display: block; text-align: center; font-weight: 600; font-size: 14px;
    padding-left: 120px;
  }
  .location__line { white-space: nowrap; }
  .location__line b { font-weight: 600; }

  /* Back: contact card */
  .card__bands { position: absolute; inset: 0; }
  .contact { position: absolute; top: 26px; left: 44px; color: var(--white); }
  .contact__name { font-size: 22px; font-weight: 700; letter-spacing: 0.5px; text-transform: uppercase; }
  .contact__title { font-size: 17px; font-weight: 600; text-transform: uppercase; margin-bottom: 10px; }
  .contact__row {
    display: flex; align-items: center; gap: 10px; font-size: 16px; line-height: 1.5;
  }
  .contact__row svg { width: 13px; height: 13px; flex: none; }
  .brand--back { right: 40px; bottom: 56px; color: var(--green); font-size: 52px; }
  .brand--back .brand__dot { width: 44px; height: 44px; }
</style>
</head>
<body>
<main class="stage">

  <section class="card card--front">
    <div class="card__photo" role="img" aria-label="Photo of hands stretching pizza dough dusted with flour"></div>
    <div class="card__photo-shade"></div>
    <div class="brand brand--front"><span>BRU'NETTIX</span><span class="brand__dot"></span></div>
    <div class="social"><span class="social__dot"></span><span class="social__dot"></span></div>
    <div class="locations">
      <span class="location__name">Harborview</span>
      <p class="location__line">4087 Corlan Avenue, Marlow Bay, WA 97061 | <b>P : 555-481-5067</b></p>
      <span class="location__name">Crestmont Hill</span>
      <p class="location__line">7315 Wendmere Road, Marlow Bay, WA 97064 | <b>P : 555-293-8840</b></p>
    </div>
  </section>

  <section class="card card--back">
    <svg class="card__bands" viewBox="0 0 620 354" preserveAspectRatio="none" aria-hidden="true">
      <polygon points="0,0 620,0 620,212 0,172" fill="var(--red)"/>
      <polygon points="0,172 620,212 620,228 0,175" fill="var(--green)"/>
    </svg>
    <div class="contact">
      <p class="contact__name">Marco Delvane</p>
      <p class="contact__title">Founder</p>
      <p class="contact__row">
        <svg viewBox="0 0 12 12"><rect x="3" y="0.5" width="6" height="11" rx="1" fill="none" stroke="#fff" stroke-width="1.2"/></svg>
        555 512 7704
      </p>
      <p class="contact__row">
        <svg viewBox="0 0 12 12"><rect x="0.5" y="2" width="11" height="8" fill="#fff"/><path d="M0.5 2 L6 7 L11.5 2" fill="none" stroke="var(--red)" stroke-width="1"/></svg>
        name@brunettix.com
      </p>
      <p class="contact__row">
        <svg viewBox="0 0 12 12"><circle cx="6" cy="6" r="5.5" fill="#fff"/><path d="M0.5 6 H11.5 M6 0.5 V11.5" stroke="var(--red)" stroke-width="0.9"/></svg>
        www.brunettix.com
      </p>
    </div>
    <div class="brand brand--back"><span>BRU'NETTIX</span><span class="brand__dot"></span></div>
  </section>

</main>
</body>
</html>
```